Business card design for holistic health care clinic

We need a double-sided business card design for our holistic health care clinic that integrates our logo design and also its color scheme. My business is called Valmira. It is an integrative medicine clinic. You have already done the logo for me. Please ensure an elegant and upscale design that is not cluttered, but still has all the necessary information (please see below for details).

Target Market(s)

Wellness, fitness, rehabilitation for educated, well-traveled open-minded clients who are focused on natural, organic, balanced and preventive healthcare and lifestyle.

Industry/Entity Type

Medical

Contact Information for Business Card

Modern, clean.

Number of Pages Required

1 page

Font styles to use
Serif
Sans Serif

Colors

Designer to choose colors to be used in the design.

Requirements
Must have
• Logo on one side, all other information on the other side.
• Other information should include:
• Tobias Wrenfeld - DOE, CPT, LMT
• 4100 East Marrow Drive
• Austin, TX 78119
• 512 555 0148
• 818 555 0192
• info@ValmiraHealth.example
• t.wrenfeld@ValmiraHealth.example
Nice to have
• Darker background on front - but not totally black - shaded/dark gray.

```html
<!DOCTYPE html>
<html lang="en">
<head>
<meta charset="utf-8">
<title>Valmira Business Card</title>
<link rel="stylesheet" href="https://fonts.googleapis.com/css2?family=Nunito:wght@700;800&family=Roboto:wght@400;500&family=Roboto+Condensed:wght@700&display=swap">
<style>
  :root {
    --page-bg: #ece8e2;
    --card-dark: #2a2a2a;
    --brand-blue: #0a92cf;
    --ink-dark: #262626;
    --text-light: #f2f2f2;
  }
  * { margin: 0; padding: 0; box-sizing: border-box; }
  html, body {
    width: 1200px;
    height: 960px;
    overflow: hidden;
    background: var(--page-bg);
  }
  .canvas {
    position: relative;
    width: 1200px;
    height: 960px;
  }
  .card {
    position: absolute;
    width: 600px;
    height: 344px;
  }
  .card--front { left: 314px; top: 113px; background: var(--card-dark); }
  .card--back { left: 311px; top: 472px; background: var(--brand-blue); }

  .wordmark {
    position: absolute;
    font-family: "Nunito", sans-serif;
    font-weight: 800;
    line-height: 1;
    letter-spacing: 1px;
    white-space: nowrap;
  }
  .tagline {
    position: absolute;
    font-family: "Nunito", sans-serif;
    font-weight: 700;
    white-space: nowrap;
    line-height: 1;
  }

  .card--front .wordmark {
    right: 46px; top: 80px;
    font-size: 54px;
    color: var(--brand-blue);
  }
  .card--front .tagline {
    right: 46px; top: 127px;
    font-size: 16px;
    color: var(--brand-blue);
  }

  .contact {
    position: absolute;
    left: 44px; top: 206px;
    font-family: "Roboto", sans-serif;
    font-size: 15px;
    line-height: 19.5px;
    color: var(--text-light);
  }
  .contact .label { color: var(--brand-blue); font-weight: 500; }
  .contact .address { margin-top: 4px; }

  .person {
    position: absolute;
    right: 43px; top: 204px;
    text-align: right;
  }
  .person .name {
    font-family: "Roboto Condensed", sans-serif;
    font-weight: 700;
    font-size: 21px;
    line-height: 24px;
    color: var(--brand-blue);
  }
  .person .credentials {
    font-family: "Roboto Condensed", sans-serif;
    font-weight: 700;
    font-size: 11.5px;
    line-height: 15px;
    color: var(--brand-blue);
  }
  .person .email {
    margin-top: 6px;
    font-family: "Roboto", sans-serif;
    font-size: 14.5px;
    color: var(--text-light);
  }

  .website {
    position: absolute;
    left: 44px; top: 292px;
    font-family: "Roboto", sans-serif;
    font-size: 15px;
    letter-spacing: 2.6px;
    color: var(--text-light);
  }
  .accent-bar {
    position: absolute;
    left: 271px; right: 44px; top: 297px;
    height: 9px;
    background: var(--brand-blue);
  }
  .card--front .website { letter-spacing: 1.2px; }

  .card--back .wordmark {
    left: 0; right: 0; top: 150px;
    text-align: center;
    font-size: 62px;
    color: var(--ink-dark);
  }
  .card--back .tagline {
    left: 0; right: 0; top: 212px;
    text-align: center;
    font-size: 17px;
    color: var(--ink-dark);
  }
  .slogan {
    position: absolute;
    left: 0; right: 0; top: 292px;
    text-align: center;
    font-family: "Roboto", sans-serif;
    font-size: 14.5px;
    color: var(--ink-dark);
  }
</style>
</head>
<body>
<main class="canvas">
  <section class="card card--front" aria-label="Card front">
    <div class="wordmark">VALMIRA</div>
    <div class="tagline">Integrative Holistic Medicine</div>

    <div class="contact">
      <div><span class="label">P:</span> 512 555 0148</div>
      <div><span class="label">C:</span> 818 555 0192</div>
      <div class="address">4100 East Marrow Drive, Austin, TX 78119</div>
    </div>

    <div class="person">
      <div class="name">TOBIAS WRENFELD</div>
      <div class="credentials">DOE, CPT, LMT</div>
      <div class="email">t.wrenfeld@ValmiraHealth.example</div>
    </div>

    <div class="website">www.ValmiraHealth.example</div>
    <div class="accent-bar"></div>
  </section>

  <section class="card card--back" aria-label="Card back">
    <div class="wordmark">VALMIRA</div>
    <div class="tagline">Integrative Holistic Medicine</div>
    <div class="slogan">it’s all about you – your health, your objectives</div>
  </section>
</main>
</body>
</html>
```